A new presentation to our clients

we are a Real Estate agency, our website is www.lumibrasa.com and it’s time to have a new, fashion and remarcable Business Card. we want to differentiate ourselves from other companies so we want a business card that differentiates us. we want the business card to impact our customers. in the competitive market that we have today, we have to be different and it is this difference that we seek

Target Market(s)

Real Estate Clients

Contact Information for Business Card

We search a totaly diferent card from the usual

Font styles to use
Sans Serif

Colors
e34197

Requirements
Must have
• Logo, adress, phone contact, e-mail, photo, and our website
Nice to have
• We would like to see a modern business card
Should not have
• Houses or building draws

```html
<!DOCTYPE html>
<html lang="en">
<head>
<meta charset="utf-8">
<title>Lumi Brasa – Business Card</title>
<link rel="stylesheet" href="https://fonts.googleapis.com/css2?family=Roboto:wght@400;500;700&display=swap">
<style>
  :root {
    --brand-pink: #e5206b;
    --card-white: #ffffff;
    --text-grey: #5a5a5a;
    --title-grey: #7d7d7d;
    --backdrop: #ecebe8;
  }
  * { margin: 0; padding: 0; box-sizing: border-box; }
  html, body {
    width: 1125px;
    height: 1200px;
    overflow: hidden;
    background: var(--backdrop);
    font-family: "Roboto", Arial, sans-serif;
  }
  .business-card {
    position: absolute;
    left: 150px;
    top: 365px;
    width: 824px;
    height: 470px;
    background: var(--card-white);
    overflow: hidden;
  }
  .contact-band {
    position: absolute;
    inset: 0;
  }
  .contact-band polygon { fill: var(--brand-pink); }
  .brand-name {
    position: absolute;
    right: 40px;
    top: 46px;
    font-size: 60px;
    font-weight: 500;
    color: var(--brand-pink);
    letter-spacing: 0.5px;
    line-height: 1;
  }
  .person {
    position: absolute;
    left: 39px;
    top: 252px;
  }
  .person-name {
    font-size: 29px;
    font-weight: 700;
    color: var(--brand-pink);
    line-height: 1.1;
  }
  .person-title {
    font-size: 19px;
    font-weight: 500;
    color: var(--title-grey);
    line-height: 1.2;
  }
  .contact-list {
    position: absolute;
    left: 40px;
    top: 349px;
    list-style: none;
  }
  .contact-item {
    display: flex;
    align-items: center;
    height: 26.5px;
    color: var(--card-white);
    font-size: 20px;
  }
  .contact-icon {
    width: 20px;
    height: 20px;
    margin-right: 10px;
    fill: var(--card-white);
  }
  .office-address {
    position: absolute;
    right: 40px;
    top: 376px;
    text-align: right;
    font-size: 20px;
    color: var(--text-grey);
    line-height: 25px;
    font-style: normal;
  }
</style>
</head>
<body>
  <div class="business-card">
    <svg class="contact-band" width="824" height="470" viewBox="0 0 824 470" aria-hidden="true">
      <polygon points="0,327 380,327 417,446 824,446 824,470 0,470"/>
    </svg>

    <div class="brand-name">Lumi Brasa</div>

    <div class="person">
      <div class="person-name">RUI MATOS</div>
      <div class="person-title">CEO/FOUNDER</div>
    </div>

    <ul class="contact-list">
      <li class="contact-item">
        <svg class="contact-icon" viewBox="0 0 24 24" aria-hidden="true"><path d="M6.6 10.8c1.4 2.8 3.8 5.1 6.6 6.6l2.2-2.2c.3-.3.7-.4 1-.2 1.1.4 2.3.6 3.6.6.6 0 1 .4 1 1V20c0 .6-.4 1-1 1C10.6 21 3 13.4 3 4c0-.6.4-1 1-1h3.5c.6 0 1 .4 1 1 0 1.3.2 2.5.6 3.6.1.3 0 .7-.2 1z"/></svg>
        <span>(+351) 224 518 306</span>
      </li>
      <li class="contact-item">
        <svg class="contact-icon" viewBox="0 0 24 24" aria-hidden="true"><path d="M7 2h10v5H7zM4 8h16a2 2 0 0 1 2 2v7h-4v5H6v-5H2v-7a2 2 0 0 1 2-2zm4 9v3h8v-3z"/></svg>
        <span>(+351) 224 518 309</span>
      </li>
      <li class="contact-item">
        <svg class="contact-icon" viewBox="0 0 24 24" aria-hidden="true"><path d="M2 5h20v14H2zm2 2v.5l8 5 8-5V7zm0 2.8V17h16V9.8l-8 5z"/></svg>
        <span>geral@lumibrasa.com</span>
      </li>
      <li class="contact-item">
        <svg class="contact-icon" viewBox="0 0 24 24" aria-hidden="true"><path d="M12 2a10 10 0 1 0 0 20 10 10 0 0 0 0-20zm-1 17.9A8 8 0 0 1 4.2 10L9 14.8v1a2 2 0 0 0 2 2zm6.9-2.5A2 2 0 0 0 16 16h-1v-3a1 1 0 0 0-1-1H8v-2h2a1 1 0 0 0 1-1V7h2a2 2 0 0 0 2-2v-.4a8 8 0 0 1 2.9 12.8z"/></svg>
        <span>www.lumibrasa.com</span>
      </li>
    </ul>

    <address class="office-address">
      Av. Marquês de Sá, 417<br>
      4470-152, Maia
    </address>
  </div>
</body>
</html>
```